Business Card Design of an established Waste Management, Plastic Recycling and Renewable Energy Comp

We are looking for business card design for plastic card with holograms (Very similar to credit card). I will provide our logo (Quenbys). So the name on the business card will be our logo )Quenbys) + Environmental next to it, so it will read Quenbys Environmental. The font for Environmental does not to be the same as the font of the logo. The holograms will be used to display ISO14001 Certified (In normal credit card, normally on the holograms, they show nova or kelo). I will post the design requirements from the card printing company very shortly to make sure they can use the design for the plastic card.

Target Market(s)

Companies, Government Organizations, Corporations.

Industry/Entity Type

Business

Contact Information for Business Card

Motto (Under the logo): Cleaner By Design
Name: Leopold Maresca; Position: Business Manager; Address: Pelmore Landfill & Recycling Facility, Tressingham Rd, Kelverton Vale, WA 6390; Ph: +61 8 5210 4738; Mob: +61 455 903 172; E: Leo@quenbysenvironmental-mail.com

Requirements
Must have
• Business Names: Quenbys Logo + Environmental word after the logo.
• Motto (Under the logo): Cleaner By Design
• All the Business Card Details above.
• Hologram Logo on the lower right corner which says: ISO 14001 Certified.
• Please remember the design will be printed on plastic card Not paper. The plastic crad is the same as credit card. Hope this helps. Thank You

```html
<!DOCTYPE html>
<html lang="en">
<head>
<meta charset="UTF-8">
<title>Quenbys Environmental – Business Card</title>
<link rel="stylesheet" href="https://fonts.googleapis.com/css2?family=Open+Sans:wght@400;600;700&display=swap">
<style>
  :root {
    --page-bg: #e9edf2;
    --frost: rgba(255, 255, 255, 0.86);
    --frost-edge: #c9d2dc;
    --navy: #123c7c;
    --ink: #3c3f44;
    --ink-soft: #4a5563;
    --brand-blue: #2f86c9;
    --back-blue-top: #3d93cf;
    --back-blue-bottom: #1668b4;
    --back-text: rgba(225, 236, 248, 0.78);
    --badge-dark: #262b33;
    --rule: #b9c2cc;
  }
  * { box-sizing: border-box; margin: 0; padding: 0; }
  html, body { width: 800px; height: 1200px; overflow: hidden; }
  body {
    background: var(--page-bg);
    font-family: "Open Sans", Arial, sans-serif;
    position: relative;
  }
  .card {
    position: absolute;
    left: 100px;
    width: 600px;
    height: 343px;
    border-radius: 16px;
    overflow: hidden;
    box-shadow: 0 10px 28px rgba(30, 50, 80, 0.18);
  }
  /* Front */
  .card--front {
    top: 128px;
    background: var(--frost);
    border: 1px solid var(--frost-edge);
  }
  .brand {
    position: absolute;
    left: 24px;
    top: 30px;
    display: flex;
    align-items: center;
    gap: 10px;
  }
  .brand__dot {
    width: 34px; height: 34px;
    border-radius: 50%;
    background: var(--brand-blue);
  }
  .brand__name {
    font-size: 38px;
    font-weight: 600;
    color: var(--ink);
    letter-spacing: -0.5px;
  }
  .person {
    position: absolute;
    right: 24px;
    top: 28px;
    text-align: right;
  }
  .person__name {
    font-size: 20px;
    font-weight: 700;
    color: var(--navy);
    line-height: 1.2;
  }
  .person__role {
    font-size: 15px;
    color: var(--ink-soft);
  }
  .edge-tab {
    position: absolute;
    right: 0; top: 20px;
    width: 14px; height: 60px;
    background: var(--brand-blue);
    border-radius: 10px 0 0 10px;
  }
  .contact {
    position: absolute;
    left: 24px;
    font-size: 15px;
    color: var(--ink-soft);
    display: flex;
    align-items: center;
    gap: 8px;
  }
  .contact svg { width: 14px; height: 14px; flex: none; }
  .contact--web { top: 176px; }
  .contact--phone { top: 257px; }
  .contact--mobile { top: 276px; }
  .contact--mail { top: 296px; }
  .divider {
    position: absolute;
    left: 24px; right: 150px; top: 202px;
    height: 1px;
    background: var(--rule);
  }
  .cert-badge {
    position: absolute;
    right: 28px; top: 185px;
    width: 130px; height: 130px;
  }
  /* Back */
  .card--back {
    top: 735px;
    background: linear-gradient(160deg, var(--back-blue-top), var(--back-blue-bottom));
    text-align: center;
    color: var(--back-text);
  }
  .back-brand {
    margin-top: 92px;
    font-size: 46px;
    font-weight: 600;
    color: #ffffff;
    letter-spacing: -0.5px;
  }
  .motto {
    margin-top: 52px;
    font-size: 14px;
    font-weight: 700;
    letter-spacing: 0.3px;
  }
  .address {
    margin-top: 14px;
    font-size: 15px;
    line-height: 1.3;
  }
</style>
</head>
<body>
  <section class="card card--front" aria-label="Business card front">
    <div class="brand">
      <span class="brand__dot"></span>
      <span class="brand__name">Quenbys</span>
    </div>
    <div class="person">
      <div class="person__name">Leopold Maresca</div>
      <div class="person__role">Business Manager</div>
    </div>
    <span class="edge-tab"></span>

    <div class="contact contact--web">
      <svg viewBox="0 0 16 16" fill="none" stroke="currentColor" stroke-width="1.3"><circle cx="8" cy="8" r="6.5"/><ellipse cx="8" cy="8" rx="3" ry="6.5"/><path d="M1.5 8h13M2.5 4.8h11M2.5 11.2h11"/></svg>
      <span>www.quenbysgroup-web.com</span>
    </div>
    <div class="divider"></div>
    <div class="contact contact--phone">
      <svg viewBox="0 0 16 16" fill="none" stroke="currentColor" stroke-width="1.4"><path d="M4 1.5l2 3-1.4 1.4c.8 2 2.5 3.7 4.5 4.5L10.5 9l3 2-1.2 2.5C7 13.5 2.5 9 2.5 3.2z"/></svg>
      <span>+61 8 5210 4738</span>
    </div>
    <div class="contact contact--mobile">
      <svg viewBox="0 0 16 16" fill="none" stroke="currentColor" stroke-width="1.4"><rect x="4" y="1.5" width="8" height="13" rx="1.5"/></svg>
      <span>+61 455 903 172</span>
    </div>
    <div class="contact contact--mail">
      <svg viewBox="0 0 16 16" fill="none" stroke="currentColor" stroke-width="1.4"><rect x="1.5" y="3.5" width="13" height="9" rx="1"/><path d="M1.5 4l6.5 5 6.5-5"/></svg>
      <span>Leo@quenbysenvironmental-mail.com</span>
    </div>

    <svg class="cert-badge" viewBox="0 0 130 130" role="img" aria-label="Certification hologram seal">
      <circle cx="65" cy="65" r="62" fill="var(--badge-dark)"/>
      <circle cx="65" cy="65" r="48" fill="var(--brand-blue)"/>
    </svg>
  </section>

  <section class="card card--back" aria-label="Business card back">
    <div class="back-brand">Quenbys</div>
    <div class="motto">CLEANER BY DESIGN</div>
    <div class="address">
      Pelmore Landfill &amp; Recycling Facility<br>
      Tressingham Rd, Kelverton Vale, WA 6390
    </div>
  </section>
</body>
</html>
```